SkyvornQ Business Cards and Stationary Design

Need a design for our business cards and stationary. I want to carry on the theme of the logo. I want the business cards to have a design on the back. I would like the business cards and the stationary to carry the same theme, design scheme, and branding

Target Market(s)

Airlines and Maintenance Facilities

Industry/Entity Type

Aviation

Contact Information for Business Card

Name
Position Title
Address: 4827 Trellis Hollow Road, Larkmere Point, Calverra, 34951
Office Number
Mobile Number
Email
Website

Font styles to use
Serif
Sans Serif

Colors

Designer to choose colors to be used in the design.

```html
<!DOCTYPE html>
<html lang="en">
<head>
<meta charset="utf-8">
<title>SkyvornQ Business Card</title>
<link rel="stylesheet" href="https://fonts.googleapis.com/css2?family=Work+Sans:wght@400;500;600&display=swap">
<style>
  :root {
    --stage: #1c1d20;
    --card-white: #ffffff;
    --card-shade: #eef0f3;
    --navy: #14264f;
    --navy-back: #25407c;
    --navy-back-deep: #1a2f62;
    --sky: #2a8fd0;
    --ink: #2b2f3a;
    --ink-soft: #4a4f5c;
    --on-navy: #e9ecf3;
  }
  * { box-sizing: border-box; margin: 0; padding: 0; }
  html, body { width: 1200px; height: 800px; overflow: hidden; }
  body {
    background: var(--stage);
    font-family: "Work Sans", Arial, sans-serif;
    position: relative;
  }
  .card {
    position: absolute;
    top: 245px;
    width: 540px;
    height: 309px;
    border-radius: 14px;
    overflow: hidden;
  }
  .card--front {
    left: 40px;
    background: linear-gradient(135deg, var(--card-shade) 0%, var(--card-white) 35%, var(--card-white) 100%);
  }
  .card--back { left: 620px; }

  .brand {
    position: absolute;
    left: 40px;
    top: 44px;
    display: flex;
    align-items: center;
    gap: 12px;
  }
  .brand__dot {
    width: 40px; height: 40px;
    border-radius: 50%;
    background: var(--sky);
  }
  .brand__name {
    font-weight: 600;
    font-size: 26px;
    letter-spacing: 6px;
    color: var(--navy);
  }

  .rule {
    position: absolute;
    left: 40px; right: 40px;
    top: 160px;
    height: 1.5px;
    background: var(--navy);
  }

  .person {
    position: absolute;
    right: 44px;
    top: 104px;
    text-align: right;
    color: var(--navy);
  }
  .person__name { font-size: 26px; font-weight: 500; letter-spacing: 1px; }
  .person__role { font-size: 14px; letter-spacing: 1px; margin-top: 2px; color: var(--ink); }

  .contacts {
    position: absolute;
    left: 40px;
    top: 176px;
    font-size: 13px;
    line-height: 19px;
    color: var(--ink-soft);
    list-style: none;
  }
  .contacts b { font-weight: 500; color: var(--ink); }

  .address {
    position: absolute;
    right: 44px;
    top: 186px;
    font-size: 13px;
    line-height: 19px;
    color: var(--ink-soft);
    text-align: right;
    font-style: normal;
  }
  .address b { font-weight: 500; color: var(--ink); }

  .accent-band {
    position: absolute;
    left: 0; bottom: 0;
    width: 250px; height: 8px;
    background: var(--sky);
    clip-path: polygon(0 0, 96% 0, 100% 100%, 0 100%);
  }
  .accent-band--navy {
    left: 240px;
    width: 300px;
    height: 5px;
    background: var(--navy);
    clip-path: none;
  }

  .back-field {
    position: absolute; inset: 0;
    background: radial-gradient(ellipse at 40% 40%, var(--navy-back) 0%, var(--navy-back-deep) 100%);
  }
  .back-brand {
    position: absolute;
    left: 0; right: 0; top: 100px;
    display: flex; justify-content: center; align-items: center; gap: 14px;
  }
  .back-brand .brand__dot { background: var(--on-navy); width: 46px; height: 46px; }
  .back-brand .brand__name { color: var(--on-navy); font-size: 32px; letter-spacing: 8px; }
  .website {
    position: absolute;
    left: 0; right: 0; top: 186px;
    text-align: center;
    font-size: 16px;
    letter-spacing: 1px;
    color: var(--on-navy);
  }
</style>
</head>
<body>
  <section class="card card--front" aria-label="Business card front">
    <div class="brand">
      <span class="brand__dot"></span>
      <span class="brand__name">SKYVORNQ</span>
    </div>
    <div class="person">
      <div class="person__name">Dana Whitlow</div>
      <div class="person__role">Director</div>
    </div>
    <div class="rule"></div>
    <ul class="contacts">
      <li><b>Mobile:</b> 0455 672 918</li>
      <li><b>Phone:</b> 555-210-4876</li>
      <li><b>Email:</b> dw@skyvornq</li>
    </ul>
    <address class="address">
      <b>Address:</b> 4827 Trellis Hollow Road<br>
      Larkmere Point, Calverra, 34951
    </address>
    <div class="accent-band"></div>
    <div class="accent-band accent-band--navy"></div>
  </section>

  <section class="card card--back" aria-label="Business card back">
    <div class="back-field" role="img" aria-label="Navy background with a faint repeated brand pattern"></div>
    <div class="back-brand">
      <span class="brand__dot"></span>
      <span class="brand__name">SKYVORNQ</span>
    </div>
    <div class="website">www.skyvornq.com</div>
  </section>
</body>
</html>
```